Counseling Practice Business Card

I need a professional looking business card incorporating my new logo that was just completed. Card needs to incorporate my name and title, description of my specialty, my address, my phone number, my fax number, my email and my website URL. I need to be able to choose design on/with different paper colors and textures.
I do not have a lot of business card ideas so I am open to anything but I want bold,sharp, clear card without additional designs other than my logo (see attached file info). I am open to different color backgrounds or paper colors including black. I do not like traditional brackets around area codes in phone number or dashes between numbers in phone number. Am open to other ways of presenting including periods between numbers as appropriate. I do not know enough to know what I like yet but I want card to coordinate and work together with my logo. My practice emphasizes natural mental health interventions so any use of color (with background paper color or the blue and green in my logo) that elicits nature is nice. In addition to black, any natural brown or wood looking background might be desirable also. Most of the offerings so far look very similar and boring.

Target Market(s)

Potential therapy clients and other professionals

Contact Information for Business Card

Card information:
Gerald M. Whitcombe, Ph.D.
Licensed Clinical Psychologist
Integrative Health Coach
4812 Marlowe Ridge Blvd SE
Suite 310
Duluth, GA 30096
(770) 415-2983 phone
(770) 581-4096 fax
drgeraldwhitcombe@quillmarsh.net
brightfernwellness.net

Font styles to use
Serif
Sans Serif
Other font styles liked:
• anything that you think looks crisp, clear and easily readable

Requirements
Must have
• Any color used should coordinate with my logo design (see attached files).
• Card should be printed horizontally so top and bottom are longest sides of rectangle.
• Background color or paper color should complement and highlight logo. Do not like a white background. black, grey, brown or any color my logo would blend well with.
Nice to have
• I would like designer to utilize color to highlight letters/name or phone-fax-web symbols.
• Bottom edge of card could be highlighted if appropriate to an idea.
Should not have
• I would NOT want the card to have a pure white background at all.
• No clear cards.
• Cards should be oriented with long sides on bottom and top, NOT sides. DO NOT LIKE THIS THIN TALL ORIENTATION.

```html
<!DOCTYPE html>
<html lang="en">
<head>
<meta charset="utf-8">
<title>Brightfern Wellness – Business Card</title>
<link rel="stylesheet" href="https://fonts.googleapis.com/css2?family=Open+Sans:wght@400;600;700&display=swap">
<style>
  :root {
    --brand-blue: #2a74b5;
    --brand-green: #0f6b35;
    --ink: #111111;
    --paper: #f2ede2;
    --stage: #ffffff;
  }
  * { margin: 0; padding: 0; box-sizing: border-box; }
  html, body { width: 1200px; height: 720px; overflow: hidden; background: var(--stage); }
  body { position: relative; font-family: "Open Sans", Arial, sans-serif; color: var(--ink); }

  .card {
    position: absolute;
    width: 444px;
    height: 274px;
    background: var(--paper);
    overflow: hidden;
    box-shadow: 8px 10px 10px rgba(0,0,0,0.28);
  }
  .card--front { left: 106px; top: 208px; }
  .card--back  { left: 646px; top: 206px; }

  .card__wave { position: absolute; left: 0; bottom: 0; width: 444px; height: 274px; }

  .brand {
    position: absolute;
    color: var(--brand-blue);
    font-weight: 600;
    text-align: center;
    line-height: 1;
  }
  .brand__dot {
    display: inline-block;
    border-radius: 50%;
    background: var(--brand-green);
    vertical-align: middle;
  }
  .brand__name { display: block; }
  .brand__sub { display: block; text-transform: uppercase; }

  .card--front .brand { left: 0; width: 444px; top: 102px; }
  .card--front .brand__name { font-size: 54px; letter-spacing: -0.5px; }
  .card--front .brand__dot { width: 16px; height: 16px; margin-right: 8px; margin-top: -6px; }
  .card--front .brand__sub { font-size: 18px; letter-spacing: 10px; margin-top: 8px; padding-left: 10px; }

  .card--back .brand { left: 14px; width: 190px; top: 128px; }
  .card--back .brand__name { font-size: 30px; letter-spacing: -0.3px; }
  .card--back .brand__dot { width: 9px; height: 9px; margin-right: 5px; margin-top: -4px; }
  .card--back .brand__sub { font-size: 10.5px; letter-spacing: 5px; margin-top: 6px; padding-left: 5px; }

  .contact { position: absolute; left: 256px; top: 84px; width: 188px; }
  .contact__name { font-size: 11.5px; font-weight: 400; line-height: 1.2; white-space: nowrap; }
  .contact__title { font-size: 6.4px; line-height: 1.3; white-space: nowrap; padding-bottom: 2px; border-bottom: 2px solid var(--brand-blue); }
  .contact__address { margin-top: 12px; font-size: 8.6px; line-height: 1.45; white-space: nowrap; }
  .contact__list { list-style: none; font-size: 8.6px; line-height: 1.45; }
  .contact__list--phones { margin-top: 10px; font-weight: 700; }
  .contact__list--web { margin-top: 10px; }
  .contact__item { display: flex; align-items: center; white-space: nowrap; }
  .contact__icon { width: 10px; height: 9px; margin-right: 4px; flex: none; fill: var(--brand-green); }
</style>
</head>
<body>

<section class="card card--front" aria-label="Business card front">
  <div class="brand">
    <span class="brand__name"><span class="brand__dot"></span>Brightfern</span>
    <span class="brand__sub">Wellness</span>
  </div>
  <svg class="card__wave" viewBox="0 0 555 343" preserveAspectRatio="none" aria-hidden="true">
    <path d="M0,265 Q277,387 555,265 L555,343 L0,343 Z" fill="var(--brand-green)"/>
    <path d="M0,276 Q277,382 555,276 L555,343 L0,343 Z" fill="var(--brand-blue)"/>
  </svg>
</section>

<section class="card card--back" aria-label="Business card back">
  <div class="brand">
    <span class="brand__name"><span class="brand__dot"></span>Brightfern</span>
    <span class="brand__sub">Wellness</span>
  </div>

  <div class="contact">
    <p class="contact__name">Gerald M. Whitcombe, Ph.D.</p>
    <p class="contact__title">Licensed Clinical Psychologist / Integrative Health Coach</p>
    <p class="contact__address">4812 Marlowe Ridge Blvd SE Suite 310<br>Duluth, GA 30096</p>

    <ul class="contact__list contact__list--phones">
      <li class="contact__item">
        <svg class="contact__icon" viewBox="0 0 10 10" aria-hidden="true"><path d="M2.2,0.5 L3.6,2.6 L2.7,3.6 Q3.6,5.7 6.2,7.1 L7.3,6.2 L9.5,7.6 L8.6,9.4 Q5.2,9.6 2.6,6.9 Q0.3,4.2 0.6,1.4 Z"/></svg>
        770 415 2983
      </li>
      <li class="contact__item">
        <svg class="contact__icon" viewBox="0 0 10 10" aria-hidden="true"><path d="M2.5,0.5 H7.5 V3 H2.5 Z M0.5,3.5 H9.5 V7.5 H8 V6 H2 V7.5 H0.5 Z M2.7,6.6 H7.3 V9.5 H2.7 Z"/></svg>
        770 581 4096
      </li>
    </ul>

    <ul class="contact__list contact__list--web">
      <li class="contact__item">
        <svg class="contact__icon" viewBox="0 0 10 10" aria-hidden="true"><circle cx="5" cy="5" r="4.5"/><path d="M0.8,3.5 H9.2 M0.8,6.5 H9.2 M5,0.5 Q2.4,5 5,9.5 M5,0.5 Q7.6,5 5,9.5" stroke="#f2ede2" stroke-width="0.6" fill="none"/></svg>
        drgeraldwhitcombe@quillmarsh.net
      </li>
      <li class="contact__item">
        <svg class="contact__icon" viewBox="0 0 10 10" aria-hidden="true"><path d="M0.5,1.5 H9.5 V8.5 H0.5 Z M1.3,2.3 V7.7 H8.7 V2.3 L5,5.4 Z M1.8,2.3 L5,4.9 L8.2,2.3 Z" fill-rule="evenodd"/></svg>
        brightfernwellness.net
      </li>
    </ul>
  </div>

  <svg class="card__wave" viewBox="0 0 555 343" preserveAspectRatio="none" aria-hidden="true">
    <path d="M0,265 Q277,387 555,265 L555,343 L0,343 Z" fill="var(--brand-green)"/>
    <path d="M0,276 Q277,382 555,276 L555,343 L0,343 Z" fill="var(--brand-blue)"/>
  </svg>
</section>

</body>
</html>
```